Local fast-growing company in the service sector

We are looking for a modern business card design, which should also appear on our letterheads

Target Market(s)

Private and industrial sectors

Contact Information for Business Card

Vorname Name
Kellberger Str. 18
71298 Kellstadt
Tel.: 07146-839214-0
Name@agentur-kvtl.de

Colors
9d9d9d
919191
aaaaaa

Requirements
Must have
• The logo (file) in silver

```html
<!DOCTYPE html>
<html lang="de">
<head>
<meta charset="utf-8">
<title>KVTL Visitenkarte</title>
<link rel="stylesheet" href="https://fonts.googleapis.com/css2?family=Roboto:wght@400;500;700&display=swap">
<style>
  :root {
    --page: #ececec;
    --card-front: #f6f6f6;
    --silver: #9d9d9d;
    --silver-dark: #919191;
    --silver-light: #aaaaaa;
    --ink: #444444;
    --back-centre: #c4c5c7;
    --back-edge: #6a6a6a;
    --white: #ffffff;
  }
  * { box-sizing: border-box; margin: 0; padding: 0; }
  html, body {
    width: 1200px; height: 960px; overflow: hidden;
    background: var(--page);
    font-family: "Roboto", Arial, sans-serif;
  }
  .canvas { position: relative; width: 1200px; height: 960px; }
  .card {
    position: absolute; left: 320px; width: 602px; height: 344px;
    border-radius: 24px;
  }
  .card--front {
    top: 102px;
    background: var(--card-front);
    box-shadow: 0 2px 6px rgba(0,0,0,.15);
  }
  .brand {
    position: absolute; left: 0; right: 0; top: 152px;
    display: flex; justify-content: center; align-items: center; gap: 14px;
  }
  .brand__mark {
    width: 30px; height: 30px; border-radius: 50%;
    background: var(--silver-light);
  }
  .brand__name {
    font-weight: 700; font-size: 54px; letter-spacing: 1px;
    color: var(--silver); line-height: 1;
  }
  .front-web {
    position: absolute; left: 0; right: 0; top: 292px;
    text-align: center; font-size: 14px; letter-spacing: 6.5px;
    color: var(--ink);
  }
  .card--back {
    top: 493px;
    background: radial-gradient(circle at 56% 30%, var(--back-centre) 0%, #9a9a9b 40%, var(--back-edge) 100%);
    color: var(--white);
    box-shadow: 0 2px 6px rgba(0,0,0,.2);
  }
  .holder {
    position: absolute; right: 36px; top: 32px;
    font-weight: 500; font-size: 20px; letter-spacing: .3px;
  }
  .contact {
    position: absolute; right: 34px; top: 210px;
    text-align: right; font-size: 14px; line-height: 19px;
    font-style: normal;
  }
  .contact__address { margin-bottom: 9px; margin-right: 2px; }
  .contact__line { display: flex; justify-content: flex-end; align-items: center; gap: 8px; }
  .contact__line svg { width: 12px; height: 12px; fill: var(--white); }
</style>
</head>
<body>
<main class="canvas">
  <section class="card card--front" aria-label="Vorderseite">
    <div class="brand">
      <span class="brand__mark"></span>
      <span class="brand__name">KVTL</span>
    </div>
    <p class="front-web">www.agentur-kvtl.de</p>
  </section>

  <section class="card card--back" aria-label="Rückseite">
    <h1 class="holder">JONAS BERGER</h1>
    <address class="contact">
      <p class="contact__address">Kellberger Str. 18<br>71298 Kellstadt</p>
      <p class="contact__line">07146-839214-0
        <svg viewBox="0 0 24 24"><path d="M6.6 10.8a15.1 15.1 0 0 0 6.6 6.6l2.2-2.2a1 1 0 0 1 1-.25 11.4 11.4 0 0 0 3.6.57 1 1 0 0 1 1 1V20a1 1 0 0 1-1 1A17 17 0 0 1 3 4a1 1 0 0 1 1-1h3.5a1 1 0 0 1 1 1c0 1.25.2 2.45.57 3.57a1 1 0 0 1-.25 1z"/></svg>
      </p>
      <p class="contact__line">name@agentur-kvtl.de
        <svg viewBox="0 0 24 24"><path d="M2 5h20v14H2z M3.5 6.5 12 13l8.5-6.5" fill="var(--white)" stroke="#8a8a8a" stroke-width="1.6"/></svg>
      </p>
      <p class="contact__line">www.agentur-kvtl.de
        <svg viewBox="0 0 24 24"><circle cx="12" cy="12" r="10"/><path d="M7 8c2 0 3 1 3 3s-2 2-2 4M15 6c-1 2 1 3 2 4s0 3-1 5" stroke="#8a8a8a" stroke-width="1.8" fill="none"/></svg>
      </p>
    </address>
  </section>
</main>
</body>
</html>
```